The Velvet Rig

need a business card for a dj and sound equipment hire(rentals) business based in Melbourne. i have attached a current card get an idea. card needs to be unique professional looking.

ps.this card is not for a DJ. it's a rental business of dj equipment and pa systems.

Industry/Entity Type

Business

Font styles to use
Sans Serif
Script

Requirements
Must have
• Business Name: THE VELVET RIG
Contact Person: KIERAN MALLORY
Mobile: 047 VELVET 91
Email: KIERAN@THEVELVETRIG.COM.AU
Website: WWW.THEVELVETRIG.COM.AU
Pixelwall: WWW.PIXELWALL.CM/THEVELVETRIG.COM.AU

```html
<!DOCTYPE html>
<html lang="en">
<head>
<meta charset="utf-8">
<title>The Velvet Rig – Business Card</title>
<link rel="stylesheet" href="https://fonts.googleapis.com/css2?family=Open+Sans:ital,wght@0,400;0,600;0,700;1,400&display=swap">
<style>
  :root {
    --teal: #1f7a8c;
    --yellow: #e9cd2e;
    --ink: #0d0d0d;
    --white: #ffffff;
    --photo-dark: #3a3128;
    --photo-mid: #7a7268;
    --photo-light: #d8d4cc;
  }
  html, body {
    margin: 0;
    padding: 0;
    overflow: hidden;
    background: #ffffff;
  }
  .card {
    position: relative;
    width: 1200px;
    height: 741px;
    overflow: hidden;
    font-family: "Open Sans", Arial, sans-serif;
    background: var(--yellow);
  }
  .hero-photo {
    position: absolute;
    left: 0; top: 0;
    width: 1200px; height: 482px;
    background: linear-gradient(120deg, var(--photo-mid) 0%, #5c544b 35%, var(--photo-dark) 70%, #231d18 100%);
  }
  .contact-band {
    position: absolute;
    left: 0; top: 482px;
    width: 1200px; height: 259px;
    background: var(--yellow);
  }
  .guide-line {
    position: absolute;
    top: 482px;
    width: 1px;
    height: 259px;
    background: var(--teal);
  }
  .brand-disc {
    position: absolute;
    left: 640px; top: 27px;
    width: 518px; height: 518px;
    border-radius: 50%;
    background: var(--white);
  }
  .name-bar {
    position: absolute;
    left: 0; top: 181px;
    width: 711px; height: 248px;
    background: var(--teal);
  }
  .name-photo {
    position: absolute;
    left: 0; top: 198px;
    width: 629px; height: 202px;
    background: linear-gradient(100deg, #c9c4ba 0%, var(--photo-light) 45%, #eceae5 75%, #b9b4aa 100%);
  }
  .person-name {
    position: absolute;
    left: 106px; top: 282px;
    margin: 0;
    font-size: 46px;
    font-weight: 700;
    letter-spacing: 2px;
    color: var(--ink);
    line-height: 1;
    white-space: nowrap;
  }
  .brand-name {
    position: absolute;
    left: 728px; top: 248px;
    margin: 0;
    font-size: 62px;
    font-weight: 600;
    color: var(--teal);
    line-height: 1;
    letter-spacing: -0.5px;
    white-space: nowrap;
  }
  .brand-tagline {
    position: absolute;
    left: 730px; top: 333px;
    margin: 0;
    font-size: 26px;
    font-style: italic;
    font-weight: 400;
    color: var(--ink);
    line-height: 1;
    white-space: nowrap;
  }
  .mobile {
    position: absolute;
    left: 65px; top: 556px;
    display: flex;
    align-items: baseline;
    gap: 34px;
    color: var(--ink);
    white-space: nowrap;
  }
  .mobile-label { font-size: 22px; }
  .mobile-number { font-size: 78px; letter-spacing: 1px; line-height: 1; }
  .contact-icon {
    position: absolute;
    top: 676px;
    width: 42px; height: 42px;
  }
  .contact-text {
    position: absolute;
    top: 683px;
    margin: 0;
    font-size: 20px;
    color: var(--ink);
    line-height: 1.2;
    white-space: nowrap;
  }
</style>
</head>
<body>
  <main class="card">
    <div class="hero-photo" role="img" aria-label="Photograph of a microphone resting over a sound mixing desk"></div>
    <div class="contact-band"></div>

    <span class="guide-line" style="left:38px"></span>
    <span class="guide-line" style="left:396px"></span>
    <span class="guide-line" style="left:719px"></span>

    <div class="brand-disc"></div>

    <div class="name-bar"></div>
    <div class="name-photo" role="img" aria-label="Close-up photograph of mixing desk faders and a microphone grille"></div>
    <h1 class="person-name">KIERAN MALLORY</h1>

    <p class="brand-name">the velvet rig</p>
    <p class="brand-tagline">sound equipment hire</p>

    <div class="mobile">
      <span class="mobile-label">mobile:</span>
      <span class="mobile-number">047 VELVET 91</span>
    </div>

    <svg class="contact-icon" style="left:15px" viewBox="0 0 42 42" aria-hidden="true"><circle cx="21" cy="21" r="19" fill="none" stroke="#1f7a8c" stroke-width="3"/></svg>
    <p class="contact-text" style="left:65px">kieran@thevelvetrig.com.au</p>

    <svg class="contact-icon" style="left:375px" viewBox="0 0 42 42" aria-hidden="true"><circle cx="21" cy="21" r="19" fill="none" stroke="#1f7a8c" stroke-width="3"/></svg>
    <p class="contact-text" style="left:426px">www.thevelvetrig.com.au</p>

    <svg class="contact-icon" style="left:698px" viewBox="0 0 42 42" aria-hidden="true"><circle cx="21" cy="21" r="19" fill="none" stroke="#1f7a8c" stroke-width="3"/></svg>
    <p class="contact-text" style="left:748px">www.pixelwall.cm/thevelvetrig.com.au</p>
  </main>
</body>
</html>
```